Venture Capital firm needs modern business cards

We are a Venture Capital firm within financial services/Asset management. The industry generally has basic business cards with black, blue and maybe green/yellow design elements.
Our firm has a four-colour swoosh logo. We are based in London and want to stand out, just a little bit!, from the crowd. Our company is called LORV Investments and the 'C' stands for collaboration thus using makerswarm is a natural portal for our business card design competition. Our logo came via makerswarm too!
We use 'Venture Partner in Asset Management' as our tagline and this is Trademark registered. We operate in a conservative industry and we should not overstep our mark. The logo is colorful as it is and therefore the rest of the design should not be too fanciful.
The objective is twofold: make our logo element stick and memorable with our audience, whilst representing a conservative yet young image.
Updates
The Business Card obviously needs a field for Name, Surname, Job Title, Adress fields: Street, City, Postcode, Country, telefone and cell number, website address, etc.
We have uploaded the ai file. We trust that these are OK. If not, please advise.
Reason: We have have been busy with a client engagement. We will set the project as Guaranteed in return for the troubles we cause. Apologies for the confusion.
Thank you all for these great and creative design suggestions. The team is very happy with a number of your ideas! We will be in touch tomorrow to give individual feedback before the project closes on Friday. We look forward to working with some of you to narrow down your creations. Thank you, LORV Investments team.
All,
Target Market(s)
Financial Services Professionals, Investors, Media, 35-70 years, mainly male, well educated
Industry/Entity Type
Conservative
Requirements
Must have
- We must make use of our logo and potential tagline 'Venture Partner in Asset Management' as we are establishing a new Brand and new company in the market.
We can use 'LORV', 'LORV Investments', and 'LORV Investments'+tagline 'Venture Partner in Asset Management' or simply the four-colour swoosh plus the name of the company as part of the text. (see files)
All design elements are available in black or grey-scale if required. (grey scale swoosh attached).
Due to regulation we must have the following wording on the card in small print 'LORV Investments is an Appointed Representative of Bramwell Holdings Partnership Limited, which is authorised by the Monetary Oversight Board'.
Nice to have
- We would consider designs that make use of different printing techniques such embossing/debossing, UV spot etc.
We attach our colour palette in the files section for your reference.
Should not have
- The font we use for our company name is 'EXO' so do not use a font style that clashes with the corporate fonts, please.
Do not use other design elements than the ones we provide in the file library as part of this project.

```html
<!DOCTYPE html>
<html lang="en">
<head>
<meta charset="utf-8">
<title>LORV Investments – Business Card</title>
<link href="https://fonts.googleapis.com/css2?family=Exo:wght@500&family=Roboto+Condensed:wght@700&family=Roboto:ital,wght@0,300;0,400;1,300&display=swap" rel="stylesheet">
<style>
  :root {
    --backdrop: #e9e9ea;
    --paper: #f7f7f5;
    --ink: #4a4a4c;
    --ink-soft: #77787a;
    --ink-faint: #a2a3a5;
    --accent-green: #8cc63f;
    --brand-dot: #8cc63f;
  }
  * { box-sizing: border-box; margin: 0; padding: 0; }
  html, body { width: 1200px; height: 800px; overflow: hidden; }
  body {
    background: var(--backdrop);
    display: flex;
    align-items: center;
    justify-content: center;
    gap: 90px;
    font-family: "Roboto", Arial, sans-serif;
    color: var(--ink);
  }
  .card {
    width: 330px;
    height: 510px;
    background: var(--paper);
    box-shadow: 0 2px 6px rgba(0,0,0,0.12);
    position: relative;
    display: flex;
    flex-direction: column;
    align-items: center;
  }
  .brand {
    display: flex;
    align-items: center;
    gap: 10px;
  }
  .brand-dot {
    width: 22px; height: 22px;
    border-radius: 50%;
    background: var(--brand-dot);
  }
  .brand-name {
    font-family: "Exo", Arial, sans-serif;
    font-weight: 500;
    color: var(--ink);
    letter-spacing: 1px;
  }

  /* Back: contact side */
  .card-back { padding-top: 78px; }
  .card-back .brand-name { font-size: 40px; }
  .person-name {
    margin-top: 26px;
    font-family: "Roboto Condensed", Arial, sans-serif;
    font-weight: 700;
    font-size: 22px;
    color: var(--accent-green);
    letter-spacing: 0.5px;
  }
  .person-title {
    margin-top: 4px;
    font-style: italic;
    font-weight: 300;
    font-size: 13px;
    color: var(--ink-soft);
  }
  .contact-list {
    list-style: none;
    margin-top: 30px;
    display: flex;
    flex-direction: column;
    align-items: center;
    gap: 14px;
    font-size: 12px;
    font-weight: 300;
    color: var(--ink-soft);
    text-align: center;
    line-height: 1.45;
  }
  .contact-list svg { display: block; margin: 0 auto 5px; fill: none; stroke: var(--ink-soft); stroke-width: 1.4; }
  .regulatory {
    position: absolute;
    bottom: 24px;
    left: 30px; right: 30px;
    font-size: 6.5px;
    line-height: 1.5;
    color: var(--ink-faint);
    text-align: center;
  }

  /* Front: brand side */
  .card-front { justify-content: center; }
  .card-front .brand-name { font-size: 58px; }
  .tagline {
    margin-top: 6px;
    font-size: 9.5px;
    font-weight: 400;
    color: var(--ink-soft);
    letter-spacing: 0.3px;
    padding-left: 30px;
  }
</style>
</head>
<body>

  <section class="card card-back" aria-label="Business card, contact side">
    <div class="brand">
      <span class="brand-dot"></span>
      <span class="brand-name">LORV</span>
    </div>
    <h1 class="person-name">MARCUS ELLERY</h1>
    <p class="person-title">Graphic designer</p>
    <ul class="contact-list">
      <li>
        <svg width="10" height="14" viewBox="0 0 10 14" aria-hidden="true"><rect x="1" y="1" width="8" height="12" rx="1.5"/><line x1="4" y1="11" x2="6" y2="11"/></svg>
        +44 20 7946 0312
      </li>
      <li>
        <svg width="14" height="10" viewBox="0 0 14 10" aria-hidden="true"><rect x="1" y="1" width="12" height="8"/><polyline points="1,1 7,6 13,1"/></svg>
        http://www.lorv.net
      </li>
      <li>
        <svg width="10" height="14" viewBox="0 0 10 14" aria-hidden="true"><path d="M5 13 C2 9 1 7 1 5 A4 4 0 0 1 9 5 C9 7 8 9 5 13 Z"/><circle cx="5" cy="5" r="1.4"/></svg>
        27 Fenwick st.<br>Aldgate Row<br>London<br>EC3N 1PX
      </li>
    </ul>
    <p class="regulatory">LORV Investments is an Appointed Representative of Bramwell Holdings Partnership Limited, which is authorised by the Monetary Oversight Board</p>
  </section>

  <section class="card card-front" aria-label="Business card, brand side">
    <div class="brand">
      <span class="brand-dot"></span>
      <span class="brand-name">LORV</span>
    </div>
    <p class="tagline">Venture Partner in Asset Management</p>
  </section>

</body>
</html>
```